Pebblebrook Plots - Online-only garden installation company

Online-only garden installation company. Our demographic is middle aged / suburban women, and we anticipate Chatter driving traffic to this website, as well as referrals from garden centers. The website must be very simple in design and function.

All orders will be placed through the website, including size of garden (3 options), location in yard, payment, and scheduling of installation date.

The website should employ a 3 step process:

Step 1: Select garden size. Either an 4' X 4', 8' X 4', or 12' X 4'.

Step 2: Select a location. We would like to use google maps to look up a US address, then "drag and drop" one of the garden sizes from step 1 to the location the customer would like us to install the garden at their home.

Step 3: Pick an installation date and pay. Using an online calendar the customer will pick a date, and then pay for the installation via credit card.

The website will be linked to an email account, PebblebrookPlots@mailvale.com to inform us of orders placed.

Target Market(s)

Our demographic is middle aged / suburban women, and we anticipate Chatter driving traffic to this website, as well as referrals from garden centers.

Industry/Entity Type

Coding

Number of Pages Required

Requirements
Must have
• Scheduling and payment options.

```html
<!DOCTYPE html>
<html lang="en">
<head>
<meta charset="utf-8">
<title>Pebblebrook Plots – Online Garden Installation</title>
<link rel="stylesheet" href="https://fonts.googleapis.com/css2?family=Josefin+Slab:wght@400;600&family=Montserrat:wght@400;600;700&family=Quicksand:wght@300;500&family=Lato:wght@400&display=swap">
<style>
:root{
  --orange:#f2690d;
  --orange-dark:#d3560a;
  --white:#ffffff;
  --ink:#222222;
  --wood-1:#7a4a2b;
  --wood-2:#5c3419;
  --sky:#6fa6d8;
  --grass:#5e9a2a;
  --grass-dark:#3f7418;
  --field-text:#9a9a9a;
  --dash:#e8d9cc;
}
*{margin:0;padding:0;box-sizing:border-box}
html,body{width:1200px;height:2344px;overflow:hidden;background:var(--wood-2)}
body{position:relative;font-family:"Montserrat",sans-serif;color:var(--white)}
.abs{position:absolute}

/* header */
.site-nav{left:0;top:0;width:1200px;height:83px;background:var(--white);z-index:3}
.site-nav a{position:absolute;top:32px;font-size:15px;font-weight:600;color:var(--ink);text-decoration:none;letter-spacing:.5px}
.brand-badge{left:494px;top:-6px;width:212px;height:212px;border-radius:50%;background:var(--white);z-index:4;display:flex;flex-direction:column;align-items:center;justify-content:center}
.brand-badge .dot{width:18px;height:18px;border-radius:50%;background:var(--orange);margin-bottom:8px}
.brand-badge .name{font-family:"Montserrat",sans-serif;font-weight:600;font-size:19px;color:var(--ink);text-align:center;line-height:1.2;letter-spacing:1px}

/* hero */
.hero{left:0;top:83px;width:1200px;height:589px;background:linear-gradient(180deg,var(--sky) 0%,#a8cbe8 35%,#6b9a3c 55%,var(--grass) 80%,#78b236 100%)}
.hero-title{left:0;top:258px;width:1200px;text-align:center;font-family:"Josefin Slab",serif;font-weight:600;font-size:62px;line-height:64px;letter-spacing:2px;text-shadow:0 2px 4px rgba(0,0,0,.35)}
.hero-tagline{left:0;top:396px;width:1200px;text-align:center;font-family:"Montserrat",sans-serif;font-weight:700;font-size:27px;text-shadow:0 2px 3px rgba(0,0,0,.4)}
.btn{position:absolute;background:var(--orange);color:var(--white);border-radius:30px;font-weight:600;display:flex;align-items:center;justify-content:center;box-shadow:0 3px 0 var(--orange-dark)}
.btn-hero{left:466px;top:472px;width:268px;height:59px;font-size:22px}

/* wood section */
.wood{left:0;top:672px;width:1200px;height:1562px;background:linear-gradient(90deg,var(--wood-1),var(--wood-2) 50%,var(--wood-1))}
.vines{left:0;top:660px;width:1200px;height:60px;background:linear-gradient(180deg,var(--grass-dark),rgba(63,116,24,0))}
.section-title{left:0;top:724px;width:1200px;text-align:center;font-weight:700;font-size:41px}
.section-sub{left:0;top:780px;width:1200px;text-align:center;font-family:"Lato",sans-serif;font-size:17px}
.step-title{font-family:"Quicksand",sans-serif;font-weight:300;font-size:58px;line-height:1}
.label{font-weight:600;font-size:15px}
.size-box{position:absolute;background:var(--white)}
.size-label{position:absolute;font-weight:600;font-size:14px}
.photo{position:absolute;border:4px solid var(--white)}
.photo.active{border-color:var(--orange)}
.icon-box{position:absolute;width:52px;height:52px;background:var(--white);display:flex;align-items:center;justify-content:center}
.field{position:absolute;height:52px;background:var(--white);border-radius:26px;display:flex;align-items:center;justify-content:space-between;padding:0 22px 0 28px;font-family:"Lato",sans-serif;font-size:14px;color:var(--field-text);box-shadow:0 2px 4px rgba(0,0,0,.25)}
.pay-option{position:absolute;top:1806px;display:flex;align-items:center;gap:8px}
.radio{width:14px;height:14px;border-radius:50%;background:var(--white);display:flex;align-items:center;justify-content:center}
.card-chip{width:47px;height:30px;background:var(--white);border-radius:3px;display:flex;align-items:center;justify-content:center;font-size:9px;font-weight:700;color:var(--ink)}
.divider{position:absolute;top:1806px;width:1px;height:30px;background:rgba(255,255,255,.5)}
.cta-line{left:258px;top:2116px;font-weight:700;font-size:40px}

/* footer */
.site-footer{left:0;top:2234px;width:1200px;height:110px;background:linear-gradient(180deg,#7fbf3a,var(--grass-dark))}
.footer-brand{left:70px;top:2258px;width:130px;text-align:center;font-weight:600;font-size:14px;line-height:1.2;display:flex;flex-direction:column;align-items:center;gap:6px}
.footer-brand .dot{width:14px;height:14px;border-radius:50%;background:var(--white)}
.footer-links a{position:absolute;top:2264px;font-family:"Lato",sans-serif;font-size:14px;color:var(--white);text-decoration:none}
.copyright{left:0;top:2296px;width:1200px;text-align:center;font-size:13px}
.copyright b{color:var(--ink);font-weight:600}
.social{position:absolute;top:2255px;width:38px;height:38px;border:2px solid var(--white);display:flex;align-items:center;justify-content:center;font-size:8px;font-weight:600;color:var(--white)}
.social.solid{background:var(--white);color:var(--ink)}
</style>
</head>
<body>

<nav class="site-nav abs">
  <a style="left:111px">HOME</a>
  <a style="left:214px">ABOUT</a>
  <a style="left:325px">CONTACT</a>
</nav>
<div class="brand-badge abs"><span class="dot"></span><span class="name">PEBBLEBROOK<br>PLOTS</span></div>

<section class="hero abs" role="img" aria-label="Sunny lawn with trees under a blue sky with clouds"></section>
<h1 class="hero-title abs">ONLINE - GARDEN<br>INSTALLATION COMPANY</h1>
<p class="hero-tagline abs">Let's Go with Green Zone for Green Life</p>
<a class="btn btn-hero">OUR PROCESS</a>

<section class="wood abs" role="img" aria-label="Vertical wooden fence planks"></section>
<div class="vines abs" role="img" aria-label="Green ivy hanging over the fence top"></div>

<h2 class="section-title abs">OUR PROCESS</h2>
<p class="section-sub abs">Easy 3 Step Process for Garden Installation</p>

<svg class="abs" style="left:0;top:0;z-index:1" width="1200" height="2344" viewBox="0 0 1200 2344" fill="none" stroke="var(--dash)" stroke-width="2" stroke-dasharray="7 6">
  <path d="M555 834 Q600 850 634 867"/>
  <path d="M1060 1190 Q900 1250 575 1310"/>
  <path d="M575 1619 Q700 1720 820 1760"/>
  <path d="M860 1990 Q800 2080 740 2100"/>
  <path d="M560 2175 Q620 2220 630 2290"/>
</svg>

<!-- Step 1 -->
<h3 class="step-title abs" style="left:126px;top:875px">Step 1 :</h3>
<p class="label abs" style="left:128px;top:946px">Select garden size. Either an</p>
<div class="size-box" style="left:128px;top:988px;width:44px;height:42px"></div>
<div class="size-box" style="left:181px;top:988px;width:125px;height:42px"></div>
<div class="size-box" style="left:317px;top:988px;width:83px;height:84px"></div>
<span class="size-label" style="left:128px;top:1043px">4' X 4'</span>
<span class="size-label" style="left:218px;top:1043px">8' X 4'.</span>
<span class="size-label" style="left:319px;top:1085px">or 12' X 4'</span>
<a class="btn" style="left:125px;top:1123px;width:167px;height:52px;font-size:16px">SELECTED</a>

<div class="photo active" style="left:634px;top:867px;width:155px;height:156px;background:linear-gradient(160deg,#4b3c2f,#a8815a)" role="img" aria-label="Small raised wooden garden bed"></div>
<div class="photo" style="left:634px;top:1034px;width:155px;height:154px;background:linear-gradient(160deg,#6e8a4a,#b99668)" role="img" aria-label="Empty raised bed frame on lawn"></div>
<div class="photo" style="left:802px;top:867px;width:320px;height:321px;background:linear-gradient(170deg,#3b4a2c 0%,#4a3b2f 40%,#c49a68 70%,#a6a39c 100%)" role="img" aria-label="L-shaped raised cedar garden beds filled with soil"></div>

<!-- Step 2 -->
<div class="icon-box" style="left:156px;top:1308px">
  <svg width="18" height="24" viewBox="0 0 18 24"><path d="M9 0C4 0 0 4 0 9c0 6 9 15 9 15s9-9 9-15c0-5-4-9-9-9z" fill="#2f8a3b"/><circle cx="9" cy="9" r="3.5" fill="#fff"/></svg>
</div>
<div class="icon-box" style="left:156px;top:1370px">
  <svg width="24" height="24" viewBox="0 0 24 24"><rect x="2" y="2" width="20" height="20" fill="none" stroke="#2f8a3b" stroke-width="3"/></svg>
</div>
<div class="abs" style="left:234px;top:1308px;width:341px;height:311px;border:4px solid var(--white);background:linear-gradient(135deg,#ece6da,#dfe5d2 50%,#ece3d6)" role="img" aria-label="Street map of the customer's area"></div>

<h3 class="step-title abs" style="left:706px;top:1312px">Step 2 :</h3>
<div class="field" style="left:708px;top:1391px;width:331px">Residential Address
  <svg width="14" height="18" viewBox="0 0 18 24"><path d="M9 0C4 0 0 4 0 9c0 6 9 15 9 15s9-9 9-15c0-5-4-9-9-9z" fill="#666"/><circle cx="9" cy="9" r="3.5" fill="#fff"/></svg></div>
<div class="field" style="left:708px;top:1453px;width:247px">Select a Date
  <svg width="15" height="15" viewBox="0 0 16 16"><rect x="1" y="3" width="14" height="12" fill="none" stroke="#666" stroke-width="2"/><path d="M1 7h14M5 1v4M11 1v4" stroke="#666" stroke-width="2"/></svg></div>
<p class="label abs" style="left:708px;top:1521px;font-size:14px">Select a location Where you Want Your Garden</p>
<a class="btn" style="left:706px;top:1563px;width:166px;height:51px;font-size:16px">VIEW MAP</a>

<!-- Step 3 -->
<h3 class="step-title abs" style="left:126px;top:1690px">Step 3 :</h3>
<p class="label abs" style="left:128px;top:1772px">Select Payment Option :</p>
<div class="pay-option" style="left:125px"><span class="radio"><svg width="10" height="8" viewBox="0 0 10 8"><path d="M1 4l3 3 5-6" stroke="#222" stroke-width="2" fill="none"/></svg></span><span class="card-chip">Vantra</span></div>
<span class="divider" style="left:218px"></span>
<div class="pay-option" style="left:240px"><span class="radio"></span><span class="card-chip">Merilo</span></div>
<span class="divider" style="left:336px"></span>
<div class="pay-option" style="left:357px"><span class="radio"></span><span class="card-chip">Amplex</span></div>
<span class="divider" style="left:454px"></span>
<div class="pay-option" style="left:476px"><span class="radio"></span><span class="card-chip">Dyscor</span></div>
<p class="label abs" style="left:128px;top:1864px">Credit Card Details :</p>
<div class="field" style="left:125px;top:1895px;width:427px">Card Number
  <svg width="18" height="14" viewBox="0 0 18 14"><rect x="1" y="1" width="16" height="12" rx="2" fill="none" stroke="#666" stroke-width="2"/><path d="M1 5h16" stroke="#666" stroke-width="2"/></svg></div>
<div class="field" style="left:125px;top:1958px;width:208px">Expiration Date
  <svg width="15" height="15" viewBox="0 0 16 16"><rect x="1" y="3" width="14" height="12" fill="none" stroke="#666" stroke-width="2"/><path d="M1 7h14M5 1v4M11 1v4" stroke="#666" stroke-width="2"/></svg></div>
<div class="field" style="left:344px;top:1958px;width:208px">Security Code
  <svg width="13" height="16" viewBox="0 0 13 16"><rect x="1" y="7" width="11" height="8" fill="#666"/><path d="M3.5 7V4.5a3 3 0 016 0V7" stroke="#666" stroke-width="2" fill="none"/></svg></div>
<a class="btn" style="left:125px;top:2020px;width:208px;height:52px;font-size:16px">PROCEED PAYMENT</a>

<div class="abs" style="left:609px;top:1766px;width:504px;height:234px;border-radius:16px;background:linear-gradient(120deg,#e9dfb8 0%,#f3f3f3 35%,#1f4f8f 60%,#d9342b 100%);opacity:.9" role="img" aria-label="Stack of payment cards and a cheque book"></div>

<h2 class="cta-line abs">MAKE YOUR PAYMENY</h2>
<a class="btn" style="left:773px;top:2116px;width:166px;height:50px;font-size:16px">PAY NOW</a>

<!-- footer -->
<footer class="site-footer abs" role="img" aria-label="Strip of green grass"></footer>
<div class="footer-brand abs"><span class="dot"></span><span>PEBBLEBROOK<br>PLOTS</span></div>
<nav class="footer-links">
  <a style="left:409px">About</a>
  <a style="left:472px">Terms</a>
  <a style="left:542px">Privacy</a>
  <a style="left:612px">Contact</a>
</nav>
<p class="copyright abs">© <b>PEBBLEBROOK PLOTS</b> - 2017. All Rights Reserved</p>
<span class="social solid" style="left:925px">Chatter</span>
<span class="social" style="left:977px">Loopa</span>
<span class="social" style="left:1028px">Snapsy</span>
<span class="social" style="left:1080px">Linkwell</span>

</body>
</html>
```